Brand New Product Needs Sales Focused Website Design

Looking for design of Homepage, Category Page & Product Page for single product sales focused website. TrundleCrate manufacture and distribute a brand new product to the market called PalTote-Case which is a super strong, re-useable, folding & stacking plastic box which can be seen on our current website www.paltote-case.example PalTote-Case was originally developed as an alternative to supermarket carrier bags and was pitched as a box for life against the other low end re-useable products. The original version was made from recycled plastic and pitched very much as environmental product. We are now taking a different direction and have re-designed the boxes in 5 bright and fashionable designs and although we still want the primary focus to be supermarket shopping we want to position the product as a design led, must have shopping and household accessory rather than a boring, cheap looking black plastic box. The new designs will still have the environmental benefits of being able to be re-used thousands of times and being 100% recyclable and save on the imminent 5p tax on carrier bags in the UK however the new designs will not be made from recycled material. Although the main use for PalTote-Case is supermarket shopping it has a multitude of other uses especially where you need temporary storage - laundry, back of the car, moving house/students, gardening, days out, home office filing (will take A4 file), recycling and much more - PalTote-Case is made out of super strong Polypropylene and can be easily washed and sanitised after use and can be folded and unfolded thousands of times and so will last for many years. PalTote-Case is a product that needs to be seen in action to be understood so the web design must quickly and easily communicate what PalTote-Case is and how it works - this can be done with video, images and copy. Our current website does not work for many reasons:- it is too busy, has too much information, tries too hard and ultimately isn't working. Any of the images off our current website can be supplied for use. Once the concept of the website is agreed I can get these photoshopped with the new designs. Pictures of new designs for reference will be attached to this brief. Ultimately we want the website to convert visitors to sales and therefore designers with a proven track record in this field are especially welcome to enter. We also have a Dropbox folder with over 100 product and situation images in - please send email address and we will send an invite to the folder. Due to Christmas period this competition will be run over 15 days however we may choose to extend the deadline to account for the non working days. Any questions feel free to ask - we will respond within 24 hours where possible.

```html
<!DOCTYPE html>
<html lang="en">
<head>
<meta charset="utf-8">
<title>PalTote Case — Home</title>
<link rel="stylesheet" href="https://fonts.googleapis.com/css2?family=Open+Sans:wght@400;600;700&family=Pinyon+Script&display=swap">
<style>
:root{
  --green:#a5c93a;
  --green-dark:#8bb12a;
  --blue:#2b50be;
  --blue-deep:#1f3fa6;
  --title-blue:#1f46b4;
  --topbar:#e3e3e3;
  --ink:#333;
  --muted:#777;
  --card-border:#dcdcdc;
  --footer:#eeeeee;
  --rule:#444;
}
*{box-sizing:border-box;margin:0;padding:0}
html,body{width:731px;height:1200px;overflow:hidden;background:#fff}
body{position:relative;font-family:"Open Sans",Arial,sans-serif;color:var(--ink)}
.abs{position:absolute}

/* top utility bar */
.utility-bar{left:0;top:0;width:731px;height:26px;background:var(--topbar)}
.utility-links{right:30px;top:9px;font-size:6.5px;color:#555;letter-spacing:.3px;word-spacing:2px}
.utility-links span{margin:0 5px}

/* header */
.site-header{left:0;top:26px;width:731px;height:72px;background:var(--green)}
.brand{left:60px;top:27px;font-size:26px;font-weight:600;color:#fff;line-height:1;letter-spacing:.5px}
.search{left:489px;top:10px;width:109px;height:18px;background:#fff;border:1px solid #ddd;font-size:7px;color:#999;padding:4px 7px}
.search svg{position:absolute;right:8px;top:4px}
.cart{left:616px;top:11px;display:flex;align-items:center;gap:6px;font-size:7px;font-weight:700;color:#fff}
.cart-dot{width:17px;height:17px;border-radius:50%;background:var(--blue);display:flex;align-items:center;justify-content:center;border:1.5px solid #fff}
.main-nav{left:332px;top:47px;display:flex;gap:21px;font-size:8.3px;color:#1d1d1d}
.nav-active{left:318px;top:69px;width:50px;height:3px;background:#fff}

/* hero */
.hero{left:0;top:98px;width:731px;height:307px;background:linear-gradient(180deg,var(--blue) 0%,var(--blue-deep) 100%)}
.hero-frame{left:61px;top:20px;width:609px;height:262px;background:#fff}
.hero-photo{top:4px;height:254px}
.photo-left{left:4px;width:159px;background:linear-gradient(135deg,#6d5236,#b79a72 50%,#3a2c22)}
.photo-center{left:166px;width:287px;background:linear-gradient(180deg,#5f8fc9,#3d70b3 60%,#2b4a78)}
.photo-right{left:456px;width:149px;background:linear-gradient(135deg,#8a1f25 0%,#8a1f25 40%,#c9a15e 45%,#5a3a2a 100%)}
.hero-caption{left:169px;top:168px;width:282px;height:88px;background:rgba(236,240,245,.85);text-align:center;padding-top:8px}
.hero-caption h2{font-size:24px;font-weight:400;line-height:1;color:var(--green-dark)}
.hero-caption h2 b{font-weight:400;color:var(--title-blue)}
.hero-caption p{font-size:7px;line-height:1.7;color:#555;margin-top:8px;padding:0 14px}
.hero-arrow{top:136px;width:26px;height:26px;border-radius:50%;background:#fff;display:flex;align-items:center;justify-content:center}

/* featured */
.section-title{left:66px;top:432px;width:603px;text-align:center;font-size:14.5px;font-weight:400;color:#222;letter-spacing:.3px}
.section-title::before,.section-title::after{content:"";position:absolute;top:11px;height:1px;background:#ddd;width:220px}
.section-title::before{left:0}.section-title::after{right:0}
.product-card{top:478px;width:134px;height:174px;border:4px solid var(--card-border);background:#fff;overflow:hidden;text-align:center}
.product-card.is-active{border-color:var(--green)}
.ribbon{position:absolute;left:0;top:0;width:0;height:0;border-top:34px solid var(--card-border);border-right:34px solid transparent}
.is-active .ribbon{border-top-color:var(--green)}
.ribbon-label{position:absolute;left:3px;top:6px;transform:rotate(-45deg);font-size:7px;font-weight:700;color:#fff}
.product-photo{position:absolute;left:6px;top:36px;width:118px;height:77px;background:linear-gradient(180deg,#d8d8d8 0 12%,#6b4a2e 12%,#8a6a45 60%,#3b3530 100%);border:1px solid #999}
.product-name{position:absolute;left:0;right:0;top:125px;font-size:8px;color:var(--muted)}
.product-price{position:absolute;left:0;right:0;top:141px;font-size:10.5px;font-weight:600;color:#222}
.cart-button{position:absolute;left:43px;bottom:0;width:52px;height:32px;background:var(--green);display:flex;align-items:center;justify-content:center}
.more-info{left:334px;top:674px;width:57px;height:21px;background:var(--green);border:1.5px solid #c8e08a;border-radius:5px;font-size:7.5px;color:#fff;text-align:center;line-height:18px}
.divider{left:66px;top:734px;width:600px;height:1px;background:#e5e5e5}

/* how it works */
.video-frame{left:74px;top:764px;width:240px;height:158px;background:#d0d0d0;border-radius:3px;box-shadow:0 10px 10px -6px rgba(0,0,0,.35)}
.video-still{left:5px;top:5px;width:230px;height:148px;background:linear-gradient(160deg,#fbfbfb 0 45%,#c9b6d9 60%,#8a7b6b 100%)}
.video-play{left:104px;top:60px}
.video-bar{left:0;top:129px;width:230px;height:19px;background:rgba(90,90,90,.75);font-size:8px;color:#fff;padding:4px 0 0 101px}
.how-title{left:343px;top:757px;font-size:14.5px;font-weight:400;color:var(--title-blue)}
.how-copy{left:344px;top:782px;width:312px;font-size:6.9px;line-height:1.6;color:#333;text-align:justify}
.how-copy p+p{margin-top:10px}
.quote-mark{left:348px;top:878px;font-size:26px;color:#c0262c;font-family:Georgia,serif;font-weight:700}
.promo{left:372px;top:886px;width:275px;font-family:"Pinyon Script",cursive;font-size:16px;line-height:1.3;color:#6d6d6d}
.promo span{display:block;padding-left:50px}

/* footer */
.site-footer{left:0;top:982px;width:731px;height:148px;background:linear-gradient(180deg,#e7e7e7,var(--footer) 20%,#f7f7f7)}
.footer-brand{left:60px;top:1026px;font-size:19px;font-weight:600;color:var(--title-blue);letter-spacing:.5px;line-height:1}
.pay-box{left:61px;top:1064px;width:144px;height:35px;border:1px solid #2a3b8c;background:#fff}
.pay-badge{left:13px;top:-7px;width:48px;height:12px;background:#1c3f94;border-radius:2px}
.pay-card{top:12px;width:23px;height:14px;border-radius:1px}
.footer-heading{font-size:10.5px;font-weight:600;color:#222}
.connect{left:264px;top:1015px}
.connect-copy{left:265px;top:1040px;width:140px;font-size:6.8px;line-height:1.65;color:#555}
.social{top:1089px;width:18px;height:18px;border-radius:50%;background:#2764b4;box-shadow:0 1px 2px rgba(0,0,0,.35)}
.newsletter{left:490px;top:1015px}
.news-icon{left:462px;top:1011px}
.news-copy{left:466px;top:1039px;width:170px;font-size:6.8px;font-style:italic;font-weight:700;line-height:1.3;color:#555}
.news-input{left:461px;top:1067px;width:179px;height:20px;border:1px solid #ccc;border-radius:10px;background:#f6f6f6;font-size:7px;color:#999;padding:5px 9px}
.subscribe{left:592px;top:1096px;width:48px;height:16px;background:var(--title-blue);border-radius:5px;font-size:7px;color:#fff;text-align:center;line-height:16px}
.footer-rule{left:0;top:1128px;width:731px;height:3px;background:var(--rule)}
.footer-bottom{left:0;top:1131px;width:731px;height:69px;background:var(--green);text-align:center;color:#fff;font-size:8.3px;line-height:14px;padding-top:15px}
.footer-bottom span{margin:0 9px}
</style>
</head>
<body>

<div class="abs utility-bar">
  <div class="abs utility-links">ACCOUNT<span>|</span>WISHLIST<span>|</span>CHECKOUT<span>|</span>LOGIN<span>|</span>SIGNUP</div>
</div>

<header class="abs site-header">
  <div class="abs brand">PalTote Case</div>
  <div class="abs search">Search ...
    <svg width="10" height="10" viewBox="0 0 10 10"><circle cx="3.5" cy="3.5" r="2.5" fill="none" stroke="#222" stroke-width="1.4"/><line x1="5.5" y1="5.5" x2="9" y2="9" stroke="#222" stroke-width="1.6"/></svg>
  </div>
  <div class="abs cart"><span class="cart-dot"><svg width="9" height="8" viewBox="0 0 9 8"><path d="M0 1h2l1 4h5l1-3H2.5" fill="none" stroke="#fff" stroke-width="1"/><circle cx="3.5" cy="7" r=".8" fill="#fff"/><circle cx="7" cy="7" r=".8" fill="#fff"/></svg></span>CART (0)</div>
  <nav class="abs main-nav"><span>HOME</span><span>WHAT</span><span>DO YOU RETHINK</span><span>PLASTIC PILLUTION</span><span>VIDEOS</span></nav>
  <div class="abs nav-active"></div>
</header>

<section class="abs hero">
  <div class="abs hero-frame">
    <div class="abs hero-photo photo-left" role="img" aria-label="Wicker-pattern tote case with brand tag"></div>
    <div class="abs hero-photo photo-center" role="img" aria-label="Blue satchel-style tote case with buckles"></div>
    <div class="abs hero-photo photo-right" role="img" aria-label="Leopard-print tote case with red lid"></div>
    <div class="abs hero-caption">
      <h2>PALTOTE <b>CASE</b></h2>
      <p>simply dummy text of the printing and typesetting industry. Lorem Ipsum has been the industry's standard dummy text ever since the 1500s, when an unknown .</p>
    </div>
  </div>
  <div class="abs hero-arrow" style="left:47px"><svg width="8" height="12" viewBox="0 0 8 12"><path d="M6 1L1.5 6 6 11" fill="none" stroke="#aaa" stroke-width="1.3"/></svg></div>
  <div class="abs hero-arrow" style="left:657px"><svg width="8" height="12" viewBox="0 0 8 12"><path d="M2 1l4.5 5L2 11" fill="none" stroke="#aaa" stroke-width="1.3"/></svg></div>
</section>

<h3 class="abs section-title">Featured Products</h3>

<article class="abs product-card is-active" style="left:74px">
  <div class="ribbon"></div><span class="ribbon-label">New</span>
  <div class="product-photo" role="img" aria-label="Wicker-pattern tote case"></div>
  <div class="cart-button"><svg width="22" height="20" viewBox="0 0 22 20"><path d="M2 7h18l-2.5 11h-13z" fill="none" stroke="#fff" stroke-width="1.4"/><path d="M7 7l4-5 4 5" fill="none" stroke="#fff" stroke-width="1.4"/><line x1="5" y1="11" x2="17" y2="11" stroke="#fff"/><line x1="5.5" y1="14" x2="16.5" y2="14" stroke="#fff"/></svg></div>
</article>
<article class="abs product-card" style="left:225px">
  <div class="ribbon"></div><span class="ribbon-label">New</span>
  <div class="product-photo" role="img" aria-label="Wood-crate pattern tote case"></div>
  <div class="product-name">ectus arcu rhoncus purus</div><div class="product-price">$158.07</div>
</article>
<article class="abs product-card" style="left:372px">
  <div class="ribbon"></div><span class="ribbon-label">New</span>
  <div class="product-photo" role="img" aria-label="Wicker-pattern tote case"></div>
  <div class="product-name">ectus arcu rhoncus purus</div><div class="product-price">$158.07</div>
</article>
<article class="abs product-card" style="left:518px">
  <div class="ribbon"></div><span class="ribbon-label">New</span>
  <div class="product-photo" role="img" aria-label="Wood-crate pattern tote case"></div>
  <div class="product-name">ectus arcu rhoncus purus</div><div class="product-price">$158.07</div>
</article>

<div class="abs more-info">More info</div>
<div class="abs divider"></div>

<div class="abs video-frame">
  <div class="abs video-still" role="img" aria-label="Product video still: presenter holding a tote case beside a filled shopping case">
    <svg class="abs video-play" width="38" height="38" viewBox="0 0 38 38"><circle cx="19" cy="19" r="16" fill="rgba(255,255,255,.6)" stroke="#333" stroke-width="3"/><path d="M15 11l12 8-12 8z" fill="#333"/></svg>
    <div class="abs video-bar">00:00:03:00</div>
  </div>
</div>

<h3 class="abs how-title">How It Works !</h3>
<div class="abs how-copy">
  <p>Lorem Ipsum is simply dummy text of the printing and typesetting industry. Lorem Ipsum has been the industry's standard dummy text ever since the 1500s, when an unknown printer took a galley of type and scrambled it to make a type specimen book. It has survived not only five centuries, but also the leap into electronic typesetting,</p>
  <p>It was popularised in the 1960s with the release of Typesheet sheets containing Lorem Ipsum passages, and more recently with desktop publishing software like Layoutly Pro including versions of Lorem Ipsum.</p>
</div>
<div class="abs quote-mark">&ldquo;</div>
<div class="abs promo">Your promotional text here Vivamus<span>volutpat ante, sit amet semper nisi</span></div>

<footer class="abs site-footer"></footer>
<div class="abs footer-brand">PalTote Case</div>
<div class="abs pay-box" role="img" aria-label="Accepted payment methods">
  <div class="abs pay-badge"></div>
  <div class="abs pay-card" style="left:8px;background:#d8432b"></div>
  <div class="abs pay-card" style="left:42px;background:#1c3f94"></div>
  <div class="abs pay-card" style="left:76px;background:#3a8fd1"></div>
  <div class="abs pay-card" style="left:110px;background:#e58a2a"></div>
</div>

<div class="abs footer-heading connect">Connect With Us</div>
<div class="abs connect-copy">Click on the social media icons below and stay connected with us across the web and throughout your day.</div>
<div class="abs social" style="left:275px"></div>
<div class="abs social" style="left:302px"></div>
<div class="abs social" style="left:330px;background:#e5632a"></div>
<div class="abs social" style="left:357px;background:#3bb0e3"></div>

<svg class="abs news-icon" width="24" height="20" viewBox="0 0 24 20"><rect x="2" y="6" width="17" height="12" fill="#fff" stroke="#2a4fa8"/><path d="M2 6l8.5 6 8.5-6" fill="none" stroke="#2a4fa8"/><path d="M10 11L22 1" stroke="#2a4fa8" stroke-width="2"/></svg>
<div class="abs footer-heading newsletter">Subscribe to newsletter</div>
<div class="abs news-copy">Lorem Ipsum is simply dummy text of the printing and typesetting</div>
<div class="abs news-input">Enter Newsletter</div>
<div class="abs subscribe">Subscribe</div>

<div class="abs footer-rule"></div>
<div class="abs footer-bottom">
  Home<span>|</span>What do you rethink<span>|</span>Plastic Pollution<span>|</span>Videos<br>
  PalTote Case Website designed by designhub &amp; managed by Webnorthline<br>
  Copyright &copy; 2014
</div>

</body>
</html>
```